Brand New Product Needs Sales Focused Website Design

Looking for design of Homepage, Category Page & Product Page for single product sales focused website. TrundleCrate manufacture and distribute a brand new product to the market called PalTote-Case which is a super strong, re-useable, folding & stacking plastic box which can be seen on our current website www.paltote-case.example PalTote-Case was originally developed as an alternative to supermarket carrier bags and was pitched as a box for life against the other low end re-useable products. The original version was made from recycled plastic and pitched very much as environmental product. We are now taking a different direction and have re-designed the boxes in 5 bright and fashionable designs and although we still want the primary focus to be supermarket shopping we want to position the product as a design led, must have shopping and household accessory rather than a boring, cheap looking black plastic box. The new designs will still have the environmental benefits of being able to be re-used thousands of times and being 100% recyclable and save on the imminent 5p tax on carrier bags in the UK however the new designs will not be made from recycled material. Although the main use for PalTote-Case is supermarket shopping it has a multitude of other uses especially where you need temporary storage - laundry, back of the car, moving house/students, gardening, days out, home office filing (will take A4 file), recycling and much more - PalTote-Case is made out of super strong Polypropylene and can be easily washed and sanitised after use and can be folded and unfolded thousands of times and so will last for many years. PalTote-Case is a product that needs to be seen in action to be understood so the web design must quickly and easily communicate what PalTote-Case is and how it works - this can be done with video, images and copy. Our current website does not work for many reasons:- it is too busy, has too much information, tries too hard and ultimately isn't working. Any of the images off our current website can be supplied for use. Once the concept of the website is agreed I can get these photoshopped with the new designs. Pictures of new designs for reference will be attached to this brief. Ultimately we want the website to convert visitors to sales and therefore designers with a proven track record in this field are especially welcome to enter. We also have a Dropbox folder with over 100 product and situation images in - please send email address and we will send an invite to the folder. Due to Christmas period this competition will be run over 15 days however we may choose to extend the deadline to account for the non working days. Any questions feel free to ask - we will respond within 24 hours where possible.

```html
<!DOCTYPE html>
<html lang="en">
<head>
<meta charset="utf-8">
<title>PalTote-Case – Home</title>
<link href="https://fonts.googleapis.com/css2?family=Montserrat:wght@400;700&family=Open+Sans:wght@400;600;700&family=Lora:ital,wght@1,700&display=swap" rel="stylesheet">
<style>
:root{
  --pink:#f07672;
  --pink-dark:#e0605c;
  --teal:#2d7f7b;
  --ink:#333333;
  --muted:#666666;
  --light:#ececec;
  --panel:#f4f4f4;
  --dark:#2d2d2d;
  --darker:#1c1c1c;
  --white:#ffffff;
  --box-blue:#2f4fc0;
  --box-navy:#1b2f86;
}
*{box-sizing:border-box;margin:0;padding:0}
html,body{width:1200px;height:3881px;overflow:hidden}
body{position:relative;font-family:"Open Sans",Arial,sans-serif;color:var(--ink);background:var(--white)}
.abs{position:absolute}
.heading{font-family:"Montserrat",Arial,sans-serif;font-weight:700;text-transform:uppercase}
.btn{position:absolute;display:flex;align-items:center;justify-content:center;font-family:"Montserrat",Arial,sans-serif;font-weight:700;font-size:12px;color:var(--white);background:var(--pink);text-transform:uppercase;letter-spacing:.5px}
.brand{font-family:"Montserrat",Arial,sans-serif;font-weight:700;color:var(--pink)}

/* header */
.site-header{top:0;left:0;width:1200px;height:104px;background:var(--white)}
.site-header .brand{position:absolute;left:40px;top:30px;font-size:36px;display:flex;align-items:center;gap:10px}
.site-header .brand i{display:block;width:18px;height:18px;background:var(--pink);border-radius:50%}
.main-nav{position:absolute;left:362px;top:0;height:104px;display:flex}
.main-nav a{display:flex;align-items:center;justify-content:center;height:104px;font-family:"Montserrat",Arial,sans-serif;font-weight:700;font-size:15px;color:var(--ink);text-decoration:none;text-transform:uppercase}
.main-nav a.active{background:var(--pink);color:var(--white)}

/* hero */
.hero{top:104px;left:0;width:1200px;height:614px;background:linear-gradient(100deg,#8c98a6 0%,#c9d0d6 30%,#e8e2dc 52%,#c95a5a 64%,#3553b8 74%,#24348a 86%,#6b7888 100%)}
.hero-title{left:104px;top:208px;font-size:40px;color:var(--white)}
.hero-text{left:104px;top:262px;width:440px;font-size:18px;line-height:26px;color:var(--white);font-weight:600}
.hero .shop{left:104px;top:349px;width:113px;height:39px}
.hero .demo{left:246px;top:349px;width:119px;height:39px;background:var(--pink-dark)}
.hero svg{position:absolute;top:305px}
.price-tag{position:absolute;left:742px;top:268px;width:84px;height:84px;border-radius:50%;background:var(--pink);color:var(--white);font-family:"Montserrat",Arial,sans-serif;font-weight:700;font-size:18px;display:flex;align-items:center;justify-content:center}

/* welcome */
.welcome{top:718px;left:0;width:1200px;height:569px;background:var(--light)}
.welcome-card{left:233px;top:-29px;width:291px;height:298px;background:var(--pink);color:var(--white);padding:36px 40px 0}
.welcome-card h2{font-size:24px;text-align:center;margin-bottom:18px}
.welcome-card p{font-size:15px;line-height:23px}
.corner-arrow{position:absolute;width:36px;height:32px;background:var(--white);display:flex;align-items:center;justify-content:center}
.photo{position:absolute}
.about-card{left:524px;top:269px;width:469px;height:294px;background:#e2e2e2;padding:38px 30px 0}
.about-card h2{font-size:22px;margin-bottom:16px}
.about-card p{font-size:14px;line-height:23px;color:var(--muted)}
.pink-square{position:absolute;width:46px;height:46px;background:var(--pink);display:flex;align-items:center;justify-content:center}

/* demo */
.demo-section{top:1287px;left:0;width:1200px;height:712px;background:linear-gradient(100deg,#56704a 0%,#8e9c76 35%,#a9a48c 55%,#c7a08c 70%,#7f9460 85%,#5c7d3e 100%)}
.demo-section h2{left:130px;top:95px;font-size:36px;color:var(--white)}
.demo-sub{left:130px;top:157px;font-size:20px;font-weight:700;color:var(--white)}
.demo-text{left:130px;top:204px;width:520px;font-size:15px;line-height:24px;color:var(--white)}
.demo-section .check{left:130px;top:327px;width:155px;height:30px}
.steps{left:130px;top:395px;width:935px;height:278px;display:flex}
.step{position:relative;width:187px;height:278px;background:var(--panel);text-align:center}
.step:nth-child(even){background:#e3e3e3}
.step h3{font-family:"Montserrat",Arial,sans-serif;font-size:13px;font-weight:700;text-transform:uppercase;margin-top:34px;white-space:nowrap}
.step .photo{left:20px;top:74px;width:147px;height:150px;background:radial-gradient(ellipse at 50% 60%,var(--box-blue) 0%,var(--box-navy) 48%,rgba(255,255,255,0) 72%)}
.step .mini{position:absolute;right:10px;bottom:12px;width:26px;height:22px;background:var(--pink);display:flex;align-items:center;justify-content:center}
.step:nth-child(even) .mini{background:#bdbdbd}

/* products */
.product-bar{top:1999px;left:0;width:1200px;height:64px;background:var(--pink)}
.product-bar span{position:absolute;top:20px;font-family:"Montserrat",Arial,sans-serif;font-weight:700;font-size:19px;color:var(--white)}
.slider-arrow{position:absolute;top:18px;width:30px;height:30px;background:#333;display:flex;align-items:center;justify-content:center}
.products{top:2063px;left:0;width:1200px;height:377px;background:#e5e5e5}
.product-card{position:absolute;top:46px;width:352px;height:291px;background:var(--white)}
.product-card .photo{left:14px;top:14px;width:324px;height:218px}
.sale{position:absolute;right:0;top:0;width:76px;height:46px;background:var(--pink);color:var(--white);font-family:"Montserrat",Arial,sans-serif;font-weight:700;font-size:15px;display:flex;align-items:center;justify-content:center}
.product-label{position:absolute;left:0;bottom:0;width:352px;height:46px;background:#3a3a3a;color:var(--white);font-family:"Montserrat",Arial,sans-serif;font-weight:700;font-size:14px;padding-left:18px;display:flex;align-items:center;text-transform:uppercase}
.product-label .cart{position:absolute;right:0;top:0;width:60px;height:46px;background:var(--pink);display:flex;align-items:center;justify-content:center}

/* guarantee */
.guarantee{top:2440px;left:0;width:1200px;height:325px}
.guarantee .photo{left:0;top:0;width:670px;height:325px;background:linear-gradient(180deg,#c3ccd2 0%,#8d979e 22%,#2b2f33 45%,#1d2023 70%,#3d6fb0 86%,#7d8286 100%)}
.guarantee-panel{position:absolute;left:670px;top:0;width:530px;height:325px;background:var(--teal);text-align:center;color:var(--white)}
.guarantee-panel h2{font-family:"Lora",Georgia,serif;font-style:italic;font-weight:700;font-size:30px;line-height:46px;margin-top:36px}
.guarantee-panel p{font-size:14px;line-height:23px;margin-top:20px}
.guarantee-panel .btn{left:181px;top:264px;width:197px;height:30px}

/* testimonials */
.testimonials{top:2765px;left:0;width:1200px;height:388px;background:var(--white)}
.testimonials h2{top:30px;left:0;width:1200px;text-align:center;font-size:26px}
.testimonials .sub{top:76px;left:0;width:1200px;text-align:center;font-size:15px;color:var(--muted)}
.quote{position:absolute;top:130px;width:520px;height:130px}
.quote .avatar{position:absolute;left:0;top:0;width:120px;height:120px;border-radius:50%;background:linear-gradient(160deg,#a8bf96,#5f7f4f 60%,#3e5a36)}
.quote .mark{position:absolute;left:138px;top:-8px;font-family:"Lora",Georgia,serif;font-size:44px;color:var(--pink)}
.quote p{position:absolute;left:160px;top:12px;width:360px;font-size:14px;line-height:22px;color:var(--ink)}
.quote cite{position:absolute;left:160px;top:112px;font-style:normal;font-size:13px;color:var(--muted)}
.quote-nav{position:absolute;top:334px;width:28px;height:28px;background:var(--pink);display:flex;align-items:center;justify-content:center}

/* pollution */
.pollution{top:3153px;left:0;width:1200px;height:227px;background:linear-gradient(90deg,#101010,#2c2c2c 30%,#3a3a3a 50%,#2c2c2c 70%,#101010)}
.pollution h2{top:42px;left:0;width:1200px;text-align:center;font-size:25px;color:var(--white)}
.pollution p{top:92px;left:0;width:1200px;text-align:center;font-size:16px;line-height:24px;color:var(--white)}
.pollution .btn{left:501px;top:183px;width:194px;height:32px;background:var(--white);color:var(--ink)}
.pollution .btn b{color:var(--pink);margin-left:8px}

/* awards */
.awards{top:3380px;left:0;width:1200px;height:145px;background:var(--white)}
.awards h2{top:16px;left:0;width:1200px;text-align:center;font-size:22px}
.badge{position:absolute;top:76px;height:44px;border-radius:4px}

/* footer */
.site-footer{top:3525px;left:0;width:1200px;height:324px;background:var(--dark);color:#dddddd}
.foot-col{position:absolute;top:54px}
.foot-col h4{font-family:"Montserrat",Arial,sans-serif;font-weight:700;font-size:16px;color:var(--pink);text-transform:uppercase;margin-bottom:14px}
.foot-col ul{list-style:none}
.foot-col li{font-size:14px;line-height:27px;padding-left:26px;position:relative}
.foot-col li::before{content:"";position:absolute;left:6px;top:10px;border-left:7px solid #ffffff;border-top:4px solid transparent;border-bottom:4px solid transparent}
.socials{display:flex;gap:12px}
.socials span{width:36px;height:36px;background:#444}
.socials span:first-child{background:var(--pink)}
.site-footer .brand{font-size:26px;margin-top:28px}
.reg{font-size:14px;line-height:30px;margin-top:6px}
.copyright{top:3849px;left:0;width:1200px;height:32px;background:var(--darker);color:#aaaaaa;font-size:12px;padding-left:155px;display:flex;align-items:center}
</style>
</head>
<body>

<header class="abs site-header">
  <div class="brand"><i></i>PalTote-Case</div>
  <nav class="main-nav">
    <a class="active" style="width:97px">Home</a>
    <a style="width:123px">Product</a>
    <a style="width:126px">Gallery</a>
    <a style="width:188px">Testimonials</a>
    <a style="width:155px">Guarantee</a>
    <a style="width:136px">Contact Us</a>
  </nav>
</header>

<section class="abs hero" role="img" aria-label="Woman in a store holding an open blue folding box full of toys">
  <h1 class="abs heading hero-title">PalTote-Case</h1>
  <p class="abs hero-text">The featherlight "briefcase" format means it's easy to carry one or several into the store.</p>
  <span class="btn shop">Shop Now</span>
  <span class="btn demo">Live Demo</span>
  <span class="price-tag">£14.95</span>
  <svg style="left:22px" width="24" height="56" viewBox="0 0 24 56"><path d="M20 2 L4 28 L20 54" fill="none" stroke="#fff" stroke-width="3"/></svg>
  <svg style="left:1154px" width="24" height="56" viewBox="0 0 24 56"><path d="M4 2 L20 28 L4 54" fill="none" stroke="#fff" stroke-width="3"/></svg>
</section>

<section class="abs welcome">
  <div class="abs welcome-card">
    <h2 class="heading">Welcome!</h2>
    <p>A Solid Featherlight Folding Box, So Many Everyday Practical Uses... Grocery Shopping, Laundry, Gardening, Caravan &amp; Camping And Much More...!</p>
    <span class="corner-arrow" style="left:239px;top:227px"><svg width="10" height="12" viewBox="0 0 10 12"><path d="M0 0 L10 6 L0 12Z" fill="#f07672"/></svg></span>
  </div>
  <div class="photo" role="img" aria-label="Woman holding a folded blue box like a briefcase" style="left:524px;top:-29px;width:469px;height:298px;background:linear-gradient(90deg,#ffffff 0%,#ffffff 30%,#d9a08e 42%,#2c8f6e 50%,#2f4fc0 58%,#ffffff 72%,#ffffff 100%)"></div>
  <div class="photo" role="img" aria-label="Woman carrying two stacked blue boxes of shopping" style="left:233px;top:269px;width:291px;height:294px;background:linear-gradient(180deg,#ffffff 0%,#e9d6c8 20%,#2c8f6e 34%,#d2603f 48%,#2f4fc0 62%,#1b2f86 90%,#ffffff 100%)"></div>
  <div class="abs about-card">
    <h2 class="heading">About Product!</h2>
    <p>PalTote-Case is a practical folding box which can be used countless times for a variety of everyday tasks. Terrific to take with you on your regular grocery shop. The featherlight "briefcase" format means it's easy to carry one or several into the store. Open at the checkout in seconds, fill and stack if you have a heavy load of shopping.</p>
    <span class="pink-square" style="left:417px;top:226px"><svg width="12" height="14" viewBox="0 0 12 14"><path d="M0 0 L12 7 L0 14Z" fill="#fff"/></svg></span>
  </div>
</section>

<section class="abs demo-section" role="img" aria-label="Family picnic on a lawn using folding boxes">
  <h2 class="abs heading">Take a look at our PalTote-Case</h2>
  <p class="abs demo-sub">From feather light flat-pack to rigid Stacking box in seconds!</p>
  <p class="abs demo-text">Caravan &amp; Campers who need a temporary carrying solution will find PalTote-Case's feather light weight and its ability to be folded and stored away in any nook or cranny invaluable.</p>
  <span class="btn check">Check Now
    <svg style="margin-left:10px" width="18" height="14" viewBox="0 0 18 14"><path d="M1 1 H4 L6 10 H15 L17 4 H5" fill="none" stroke="#fff" stroke-width="2"/></svg></span>
  <div class="abs steps">
    <div class="step"><h3>Folded</h3><div class="photo" role="img" aria-label="Blue box folded flat"></div><span class="mini"><svg width="8" height="10" viewBox="0 0 8 10"><path d="M0 0 L8 5 L0 10Z" fill="#fff"/></svg></span></div>
    <div class="step"><h3>Open the clip</h3><div class="photo" role="img" aria-label="Opening the clip of the blue box"></div><span class="mini"><svg width="8" height="10" viewBox="0 0 8 10"><path d="M0 0 L8 5 L0 10Z" fill="#fff"/></svg></span></div>
    <div class="step"><h3>Pull out ends</h3><div class="photo" role="img" aria-label="Pulling out the box ends"></div><span class="mini"><svg width="8" height="10" viewBox="0 0 8 10"><path d="M0 0 L8 5 L0 10Z" fill="#fff"/></svg></span></div>
    <div class="step"><h3>Slides rails to lock</h3><div class="photo" role="img" aria-label="Sliding the rails to lock the box"></div><span class="mini"><svg width="8" height="10" viewBox="0 0 8 10"><path d="M0 0 L8 5 L0 10Z" fill="#fff"/></svg></span></div>
    <div class="step"><h3>Stacks too!</h3><div class="photo" role="img" aria-label="Two open boxes stacked"></div><span class="mini"><svg width="8" height="10" viewBox="0 0 8 10"><path d="M0 0 L8 5 L0 10Z" fill="#fff"/></svg></span></div>
  </div>
</section>

<div class="abs product-bar">
  <span style="left:40px">PRODUCT</span>
  <svg class="abs" style="left:160px;top:24px" width="10" height="16" viewBox="0 0 10 16"><path d="M1 1 L9 8 L1 15" fill="none" stroke="#fff" stroke-width="2"/></svg>
  <span style="left:236px">STANDARD</span>
  <span class="slider-arrow" style="left:1090px"><svg width="8" height="12" viewBox="0 0 8 12"><path d="M8 0 L0 6 L8 12Z" fill="#fff"/></svg></span>
  <span class="slider-arrow" style="left:1126px"><svg width="8" height="12" viewBox="0 0 8 12"><path d="M0 0 L8 6 L0 12Z" fill="#fff"/></svg></span>
</div>

<section class="abs products">
  <article class="product-card" style="left:40px">
    <div class="photo" role="img" aria-label="Open box with a birds and flowers print" style="background:linear-gradient(180deg,#ffffff 0%,#ffffff 18%,#e9dfc4 30%,#c9d6b8 50%,#e9a9a0 68%,#6f9fb8 82%,#ffffff 100%)"></div>
    <span class="sale">SALE</span>
    <div class="product-label">Birds &amp; Flowers<span class="cart"><svg width="24" height="20" viewBox="0 0 24 20"><path d="M1 2 H5 L8 14 H20 L23 5 H6" fill="none" stroke="#fff" stroke-width="2.4"/><circle cx="9" cy="18" r="1.8" fill="#fff"/><circle cx="19" cy="18" r="1.8" fill="#fff"/></svg></span></div>
  </article>
  <article class="product-card" style="left:424px">
    <div class="photo" role="img" aria-label="Open box with a wooden crate print" style="background:linear-gradient(180deg,#ffffff 0%,#ffffff 20%,#a77a50 32%,#6b4a2e 55%,#3c2817 80%,#ffffff 100%)"></div>
    <span class="sale">SALE</span>
    <div class="product-label">Wooden Crate<span class="cart"><svg width="24" height="20" viewBox="0 0 24 20"><path d="M1 2 H5 L8 14 H20 L23 5 H6" fill="none" stroke="#fff" stroke-width="2.4"/><circle cx="9" cy="18" r="1.8" fill="#fff"/><circle cx="19" cy="18" r="1.8" fill="#fff"/></svg></span></div>
  </article>
  <article class="product-card" style="left:808px">
    <div class="photo" role="img" aria-label="Folded box with a leopard print" style="background:linear-gradient(180deg,#ffffff 0%,#ffffff 14%,#8a2a40 26%,#c99a5a 52%,#7a2a3e 70%,#4c1826 86%,#ffffff 100%)"></div>
    <span class="sale">SALE</span>
    <div class="product-label">Leopard<span class="cart"><svg width="24" height="20" viewBox="0 0 24 20"><path d="M1 2 H5 L8 14 H20 L23 5 H6" fill="none" stroke="#fff" stroke-width="2.4"/><circle cx="9" cy="18" r="1.8" fill="#fff"/><circle cx="19" cy="18" r="1.8" fill="#fff"/></svg></span></div>
  </article>
</section>

<section class="abs guarantee">
  <div class="photo" role="img" aria-label="Car wheels parked on blue boxes to show their strength"></div>
  <div class="guarantee-panel">
    <h2>A Box For Life<br>Guarantee Explained.</h2>
    <p>When We Say For Life We Mean For Life!<br>We Are That Confident In Our Product!</p>
    <span class="btn">Lifetime Guarantee
      <svg style="margin-left:8px" width="8" height="10" viewBox="0 0 8 10"><path d="M0 0 L8 5 L0 10Z" fill="#fff"/></svg></span>
  </div>
</section>

<section class="abs testimonials">
  <h2 class="abs heading">Testimonials</h2>
  <p class="abs sub">What Our Customers Have To Say About PalTote-Case</p>
  <blockquote class="quote" style="left:48px">
    <div class="avatar" role="img" aria-label="Customer portrait outdoors"></div>
    <span class="mark">&ldquo;</span>
    <p>An easy 5 Star from me ~ so easy to use at the checkout for my weekly shop ~ no more bags for me!</p>
    <cite>-Jo Marlow From Fernleigh</cite>
  </blockquote>
  <blockquote class="quote" style="left:640px">
    <div class="avatar" role="img" aria-label="Customer portrait outdoors"></div>
    <span class="mark">&ldquo;</span>
    <p>An easy 5 Star from me ~ so easy to use at the checkout for my weekly shop ~ no more bags for me!</p>
    <cite>-Jo Marlow From Fernleigh</cite>
  </blockquote>
  <span class="quote-nav" style="left:566px"><svg width="8" height="10" viewBox="0 0 8 10"><path d="M8 0 L0 5 L8 10Z" fill="#fff"/></svg></span>
  <span class="quote-nav" style="left:602px"><svg width="8" height="10" viewBox="0 0 8 10"><path d="M0 0 L8 5 L0 10Z" fill="#fff"/></svg></span>
</section>

<section class="abs pollution" role="img" aria-label="Dark scene of discarded plastic bags">
  <h2 class="abs heading">PalTote-Case helping to reduce plastic pollution</h2>
  <p class="abs">Plastic Pollution Is A Worldwide Problem And Is Destroying OUR Planet!<br>One Of The Worst Offenders Is ... The Plastic Carrier Bag!</p>
  <span class="btn">Join With Us<b>&#9656;</b></span>
</section>

<section class="abs awards">
  <h2 class="abs heading">Awards</h2>
  <span class="badge" style="left:275px;width:130px;background:#d9d9d9"></span>
  <span class="badge" style="left:485px;width:130px;background:#3a3a3a"></span>
  <span class="badge" style="left:663px;width:160px;background:#c8302c"></span>
  <span class="badge" style="left:890px;width:96px;background:#f2c230"></span>
</section>

<footer class="abs site-footer">
  <div class="foot-col" style="left:155px">
    <h4>Navigation</h4>
    <ul><li>Home</li><li>Gallery</li><li>Testimonials</li><li>Guarantee</li><li>Contact us</li></ul>
  </div>
  <div class="foot-col" style="left:475px">
    <h4>Product</h4>
    <ul><li>Black</li><li>Blue</li><li>Blue Satchel</li><li>Wooden Crate</li><li>Wicker Basket</li><li>Birds &amp; Flowers</li><li>Leopard</li></ul>
  </div>
  <div class="foot-col" style="left:792px">
    <h4>Followus</h4>
    <div class="socials" aria-label="Social links"><span></span><span></span><span></span><span></span></div>
    <div class="brand">PalTote-Case</div>
    <p class="reg">Reg Design no 2048113<br>Patent a pp GB2207415.6</p>
  </div>
</footer>
<div class="abs copyright">Copyright &copy; TrundleCrate Ltd 2013</div>

</body>
</html>
```